Business Card for a Jewellery Brand

Business card for an upscale jewellery brand. Attached is the brand logo and icon and color board. I am looking for two card versions: one for the founder and one is generic. The card should be elegant and convey upscale and premium feel. I am open to both square and rectangle card shapes.

Industry/Entity Type

Jewelry

Contact Information for Business Card

Two cards: (1) Sunela Parvaniya (Founder) (2) General
(1) Sunela Parvaniya card should have Name: Sunela Parvaniya, Title: Founder Email id: sunela@quiremo.com.au. Phone no: +61452913307
(2) Generic card should have Email id: info@quiremo.com.au. Phone no: +61436207518

Requirements
Must have
• Workmark
• ICON
• Phone no
• Email ID
• ABN: 58219740312 (Note: ABN is Business number in Australia)
• Website: www.quiremo.com.au
• Instagram: quiremo_jewellery
• Facebook: @quiremojewellery
Nice to have
• Tagline

```html
<!DOCTYPE html>
<html lang="en">
<head>
<meta charset="utf-8">
<title>Quiremo Business Card</title>
<link rel="stylesheet" href="https://fonts.googleapis.com/css2?family=Source+Sans+3:wght@400;600&display=swap">
<style>
  :root {
    --backdrop: #ababab;
    --card-dark: #252628;
    --brand-pink: #e59893;
    --text-light: #f2f2f2;
    --white: #ffffff;
  }
  * { margin: 0; padding: 0; box-sizing: border-box; }
  html, body {
    width: 1200px;
    height: 900px;
    overflow: hidden;
    background: var(--backdrop);
    font-family: "Source Sans 3", "Myriad Pro", Arial, sans-serif;
  }
  .stage { position: relative; width: 1200px; height: 900px; }

  .card {
    position: absolute;
    top: 200px;
    width: 310px;
    height: 501px;
  }
  .card-front {
    left: 265px;
    background: var(--card-dark);
    border-radius: 66px 0 66px 0;
  }
  .card-back {
    left: 641px;
    width: 308px;
    background: var(--brand-pink);
    border-radius: 0 66px 0 66px;
  }

  .brand-mark {
    position: absolute;
    left: 0; right: 0;
    top: 52px;
    display: flex;
    flex-direction: column;
    align-items: center;
  }
  .brand-dot {
    width: 46px; height: 46px;
    border-radius: 50%;
    background: var(--brand-pink);
    margin-bottom: 44px;
  }
  .wordmark {
    color: var(--brand-pink);
    font-weight: 400;
    font-size: 40px;
    line-height: 1;
    letter-spacing: 7px;
    padding-left: 7px;
  }

  .person { position: absolute; left: 25px; top: 261px; }
  .person-name {
    color: var(--brand-pink);
    font-weight: 600;
    font-size: 17px;
    line-height: 20px;
  }
  .person-title { color: var(--text-light); font-size: 13px; line-height: 18px; }

  .abn {
    position: absolute; left: 25px; top: 317px;
    color: var(--text-light); font-size: 13px;
  }
  .abn-label { color: var(--brand-pink); font-weight: 600; font-size: 14px; }

  .contact-list {
    position: absolute; left: 25px; top: 352px;
    list-style: none;
  }
  .contact-list li {
    display: flex; align-items: center;
    height: 21px;
    color: var(--text-light);
    font-size: 13px;
  }
  .contact-icon {
    width: 11px; height: 11px;
    margin-right: 8px;
    flex: none;
    fill: var(--brand-pink);
  }
  .social-dot {
    width: 11px; height: 11px;
    margin-right: 8px;
    flex: none;
    border-radius: 50%;
    background: var(--brand-pink);
  }

  .back-wordmark {
    position: absolute;
    left: 0; right: 0;
    top: 390px;
    text-align: center;
    color: var(--white);
    font-weight: 400;
    font-size: 50px;
    line-height: 1;
    letter-spacing: 8px;
    padding-left: 8px;
  }
</style>
</head>
<body>
<main class="stage">
  <section class="card card-front">
    <div class="brand-mark">
      <div class="brand-dot"></div>
      <div class="wordmark">QUIREMO</div>
    </div>

    <div class="person">
      <p class="person-name">Sunela Parvaniya</p>
      <p class="person-title">Founder</p>
    </div>

    <p class="abn"><span class="abn-label">ABN:</span> 58219740312</p>

    <ul class="contact-list">
      <li>
        <svg class="contact-icon" viewBox="0 0 24 24"><path d="M6.6 10.8a15.1 15.1 0 0 0 6.6 6.6l2.2-2.2c.3-.3.7-.4 1-.2 1.1.4 2.3.6 3.6.6.6 0 1 .4 1 1V20c0 .6-.4 1-1 1A17 17 0 0 1 3 4c0-.6.4-1 1-1h3.5c.6 0 1 .4 1 1 0 1.3.2 2.5.6 3.6.1.3 0 .7-.2 1z"/></svg>
        +61452913307
      </li>
      <li>
        <svg class="contact-icon" viewBox="0 0 24 24"><path d="M2 5h20v14H2z M3.5 6.5 12 13l8.5-6.5" fill="var(--brand-pink)" stroke="var(--card-dark)" stroke-width="1.8"/></svg>
        sunela@quiremo.com.au
      </li>
      <li>
        <svg class="contact-icon" viewBox="0 0 24 24"><circle cx="12" cy="12" r="10"/><path d="M2 12h20M12 2c3 3 3 17 0 20M12 2c-3 3-3 17 0 20" fill="none" stroke="var(--card-dark)" stroke-width="1.6"/></svg>
        www.quiremo.com.au
      </li>
      <li><span class="social-dot"></span>quiremo_jewellery</li>
      <li><span class="social-dot"></span>@quiremojewellery</li>
    </ul>
  </section>

  <section class="card card-back">
    <div class="back-wordmark">QUIREMO</div>
  </section>
</main>
</body>
</html>
```